MARKETING MY MEDICAL PRACTICE

I am a physician providing medical-legal evaluations for competing attorneys (applicant attorneys representing injured workers versus defense attorneys and health insurance companies representing employers). Each opposing side wants me to be more biased toward their side. I am looking for a classy/elegant graphic design to apply to an exhibit booth LED backlit display, website, and printed brochures/business cards. I like the basic feel of the uploaded files IMG 1842 and IMG 1837. My medical practice focuses on evaluating patients with nerve, muscle, and skeletal injuries. I would like to include the three football players representing the nervous, muscular, and skeletal systems as well as the tools of my trade (goniometer measuring the knee range of motion, reflex hammer, and stethoscope with judge's gavel and hammer to describe what I do). I would like the goniometer, reflex hammer, and gavel & hammer to be faded into the back ground. The football players should be less opaque and more obvious.
I want my name in large big bold letters across the top of the graphics design: GERALD P. HOLLIS, M.D.
In smaller font below my name please place: Physical Medicine
One of the pics of me should be (with the backgrounds eliminated) on the side of my name (next to GERALD, not next to M.D.). I am not sure which pic would be better or more professionally appropriate.
On the other side of my name should be the illustration of the man showing muscular, skeletal, and nervous systems. It's my logo. I will supply the actual vector file of this logo once I receive it.
Somewhere in the graphics include: QME, AME, IME, & SIBTF evaluation
Somewhere in the graphics include: Physical Medicine: The specialty for neurological and musculoskeletal injuries in one evaluation by one doctor
Attorneys who refer injured workers for evaluation
MEDICAL SERVICES

```html
<!DOCTYPE html>
<html lang="en">
<head>
<meta charset="utf-8">
<title>Gerald P. Hollis, M.D – Physical Medicine Display</title>
<link rel="stylesheet" href="https://fonts.googleapis.com/css2?family=Anton&family=Poppins:wght@300;400;600;700&display=swap">
<style>
  :root {
    --page-bg: #e6e6e6;
    --white: #ffffff;
    --brand-red: #b02a2e;
    --panel-red: #c23c3f;
    --deep-red: #8e1f23;
    --ink: #1b1b1b;
    --panel-black: #1c1c1d;
    --ring-grey: #b9b9b9;
    --text-light: #f4f1f1;
  }
  * { margin: 0; padding: 0; box-sizing: border-box; }
  html, body {
    width: 800px; height: 1200px; overflow: hidden;
    background: var(--page-bg);
  }
  .display {
    position: absolute; left: 40px; top: 312px;
    width: 720px; height: 575px;
    overflow: hidden; background: var(--panel-black);
    font-family: "Poppins", sans-serif;
  }
  .display__backdrop { position: absolute; inset: 0; }
  .headline {
    position: absolute; left: 0; right: 0; top: 22px;
    text-align: center;
  }
  .headline__name {
    font-family: "Anton", sans-serif;
    font-size: 70px; line-height: 1; letter-spacing: -0.5px;
    color: var(--brand-red);
  }
  .headline__specialty {
    font-family: "Anton", sans-serif;
    font-size: 40px; line-height: 1; margin-top: 0;
    color: var(--ink); margin-left: -14px;
  }
  .portrait {
    position: absolute; left: 0; top: 118px;
    width: 243px; height: 457px;
    background: linear-gradient(180deg, #a77f6a 0%, #a77f6a 30%, #3d6fa8 38%, #2f5f94 100%);
    border-radius: 90px 90px 0 0;
  }
  .services {
    position: absolute; left: 242px; top: 186px;
    list-style: none;
  }
  .services__item {
    display: flex; align-items: center; gap: 7px;
    height: 42.5px;
    font-weight: 700; font-size: 29px; color: var(--white); line-height: 1;
  }
  .services__icon { width: 28px; height: 28px; flex: none; }
  .services__note {
    display: block; font-size: 12px; font-weight: 700;
    margin: -6px 0 0 35px; color: var(--white); letter-spacing: 0.3px;
  }
  .divider-dots {
    position: absolute; left: 248px; top: 374px;
    display: flex; gap: 12.5px;
  }
  .divider-dots span {
    width: 4px; height: 4px; border-radius: 50%;
    background: rgba(255,255,255,0.45);
  }
  .specialty-statement {
    position: absolute; left: 248px; top: 400px; width: 175px;
    font-size: 14.5px; font-weight: 400; line-height: 20.3px;
    color: var(--text-light); text-transform: uppercase;
  }
  .system-figure {
    position: absolute; width: 96px; height: 96px; border-radius: 50%;
    background: radial-gradient(circle at 50% 50%, #2a4f9c 0%, #0d1a3a 45%, #000 75%);
    border: 2px solid var(--ring-grey);
  }
  .system-figure--nerves { left: 366px; top: 204px; }
  .system-figure--muscles { left: 390px; top: 315px;
    background: radial-gradient(circle at 50% 50%, #7a3c7a 0%, #1f1c4a 45%, #000 75%); }
  .system-figure--skeleton { left: 428px; top: 423px; }
  .practice-card {
    position: absolute; left: 478px; top: 177px;
    width: 207px; height: 76px;
    border: 2px solid var(--brand-red); border-radius: 16px;
    display: flex; align-items: center; gap: 10px; padding-left: 14px;
  }
  .practice-card__mark {
    width: 16px; height: 16px; border-radius: 50%;
    background: var(--brand-red); flex: none;
  }
  .practice-card__name {
    font-size: 11px; font-weight: 600; color: var(--text-light); line-height: 1.2;
  }
  .practice-card__field {
    font-size: 8.3px; font-weight: 400; color: var(--text-light);
    border-top: 1px solid var(--brand-red); padding-top: 3px; margin-top: 3px;
  }
  .anatomy-figure {
    position: absolute; left: 548px; top: 272px;
    width: 108px; height: 280px;
    border-radius: 50px 50px 30px 30px;
    background: linear-gradient(90deg, #e9a25a 0%, #f2c068 50%, #c8413c 100%);
  }
</style>
</head>
<body>
  <section class="display">
    <svg class="display__backdrop" viewBox="0 0 720 575" width="720" height="575" aria-hidden="true">
      <rect width="720" height="575" fill="var(--panel-black)"/>
      <path d="M0 130 H470 C500 260 520 420 520 575 H0 Z" fill="var(--panel-red)"/>
      <path d="M440 150 C470 260 495 420 505 575 H520 C518 420 500 260 462 150 Z" fill="var(--deep-red)"/>
      <path d="M0 0 H720 V102 C560 150 380 180 190 158 C110 148 50 132 0 111 Z" fill="var(--white)"/>
      <path d="M0 111 C50 132 110 148 190 158 C380 180 560 150 720 102 V106 C560 160 380 190 190 172 C110 164 50 150 0 136 Z" fill="#0f0f10"/>
    </svg>

    <header class="headline">
      <h1 class="headline__name">GERALD P. HOLLIS, M.D</h1>
      <p class="headline__specialty">PHYSICAL MEDICINE</p>
    </header>

    <div class="portrait" role="img" aria-label="Portrait photo of the physician in a blue polo shirt, arms crossed"></div>

    <ul class="services">
      <li class="services__item">
        <svg class="services__icon" viewBox="0 0 28 28" aria-hidden="true"><circle cx="14" cy="14" r="11" fill="none" stroke="#2a0b0c" stroke-width="2" stroke-dasharray="3 1.5"/><circle cx="14" cy="14" r="7.5" fill="none" stroke="#2a0b0c" stroke-width="1.5"/><path d="M10 14 l3 3 l5 -6" fill="none" stroke="#2a0b0c" stroke-width="1.8"/></svg>
        QME
      </li>
      <li class="services__item">
        <svg class="services__icon" viewBox="0 0 28 28" aria-hidden="true"><circle cx="14" cy="14" r="11" fill="none" stroke="#2a0b0c" stroke-width="2" stroke-dasharray="3 1.5"/><circle cx="14" cy="14" r="7.5" fill="none" stroke="#2a0b0c" stroke-width="1.5"/><path d="M10 14 l3 3 l5 -6" fill="none" stroke="#2a0b0c" stroke-width="1.8"/></svg>
        AME
      </li>
      <li class="services__item">
        <svg class="services__icon" viewBox="0 0 28 28" aria-hidden="true"><circle cx="14" cy="14" r="11" fill="none" stroke="#2a0b0c" stroke-width="2" stroke-dasharray="3 1.5"/><circle cx="14" cy="14" r="7.5" fill="none" stroke="#2a0b0c" stroke-width="1.5"/><path d="M10 14 l3 3 l5 -6" fill="none" stroke="#2a0b0c" stroke-width="1.8"/></svg>
        IME
      </li>
      <li class="services__item">
        <svg class="services__icon" viewBox="0 0 28 28" aria-hidden="true"><circle cx="14" cy="14" r="11" fill="none" stroke="#2a0b0c" stroke-width="2" stroke-dasharray="3 1.5"/><circle cx="14" cy="14" r="7.5" fill="none" stroke="#2a0b0c" stroke-width="1.5"/><path d="M10 14 l3 3 l5 -6" fill="none" stroke="#2a0b0c" stroke-width="1.8"/></svg>
        SIBTF
      </li>
      <li><span class="services__note">EVALUATION</span></li>
    </ul>

    <div class="divider-dots" aria-hidden="true">
      <span></span><span></span><span></span><span></span><span></span><span></span><span></span><span></span>
    </div>

    <p class="specialty-statement">The specialty for neurological and musculoskeletal injuries in one evaluation by one doctor</p>

    <div class="system-figure system-figure--nerves" role="img" aria-label="Football player figure showing the nervous system"></div>
    <div class="system-figure system-figure--muscles" role="img" aria-label="Football player figure showing the muscular system"></div>
    <div class="system-figure system-figure--skeleton" role="img" aria-label="Football player figure showing the skeletal system"></div>

    <div class="practice-card">
      <span class="practice-card__mark" aria-hidden="true"></span>
      <div>
        <p class="practice-card__name">GERALD P. HOLLIS, M.D.</p>
        <p class="practice-card__field">Physical Medicine &amp; Rehabilitation</p>
      </div>
    </div>

    <div class="anatomy-figure" role="img" aria-label="Anatomical illustration of a man showing muscular, skeletal and nervous systems"></div>
  </section>
</body>
</html>
```